Skiing Company Needs A5 28page Skiing Catalogue

ABOUT THE BUSINESS/COMPANY:
- We are a guided skiing company called "Silver Lantern Journeys" and "Kestrel Ridge Alpine Society".

ABOUT THE CATALOGUE:

- We need an A5 28 page catalogue. ALL THE FILES (like photos and logos) are in the zip folders.

- You can look at the 000 KRS Catalog Word Document. Instructions on what text and photos to use are labeled there per Page.

Target Market(s)

Advanced/ Expert Skiers and Snowboarders that are thinking of joining a tour

Industry/Entity Type

Travel Agent

Font styles to use
Serif

Colors
ffffff
ec1f27
0455a3

Requirements
Must have
• NEED a 3mm bleed
• This is included on the 000 KRS Catalog word document
Nice to have
• Our main color is dark blue (just like our logo). Some red is ok but the main focus should be the dark blue.
Should not have
• Words/ Letters in the color red

```html
<!DOCTYPE html>
<html lang="en">
<head>
<meta charset="utf-8">
<title>Kestrel Ridge Alpine Society – 2017-18 Product Catalog</title>
<link rel="stylesheet" href="https://fonts.googleapis.com/css2?family=Tinos:wght@400;700&display=swap">
<style>
  :root {
    --backdrop: #c4c4c4;
    --navy: #0c1740;
    --navy-deep: #08112f;
    --rule-red: #b3232c;
    --white: #ffffff;
    --sky-top: #dfe4ee;
    --sky-low: #eef1f6;
    --snow: #f4f6fa;
    --snow-shade: #c9d1e1;
    --ink: #1a1f33;
  }
  * { box-sizing: border-box; margin: 0; padding: 0; }
  html, body {
    width: 1200px; height: 789px; overflow: hidden;
    background: var(--backdrop);
    font-family: "Tinos", "Times New Roman", serif;
  }
  .stage {
    position: relative; width: 1200px; height: 789px;
    display: flex; align-items: center; justify-content: center;
  }
  .cover {
    position: relative; width: 540px; height: 764px;
    overflow: hidden; background: var(--snow);
    box-shadow: 0 2px 10px rgba(0,0,0,.18);
  }
  .cover-photo {
    position: absolute; inset: 0 0 30% 0;
    background:
      linear-gradient(160deg, transparent 38%, rgba(201,209,225,.55) 39%, var(--snow) 62%, var(--snow-shade) 100%),
      linear-gradient(180deg, var(--sky-top) 0%, var(--sky-low) 45%, #d9dde6 100%);
  }
  .cover-curves {
    position: absolute; inset: 0; width: 540px; height: 764px;
  }
  .lodge-mark {
    position: absolute; top: 36px; right: 26px; width: 150px;
    text-align: center; color: var(--ink);
  }
  .lodge-mark .mark-square {
    display: block; width: 14px; height: 14px; margin: 0 auto 6px;
    background: var(--ink);
  }
  .lodge-mark .mark-name {
    font-size: 16px; font-weight: 700; line-height: 1.1; letter-spacing: .5px;
  }
  .lodge-mark .mark-line {
    margin-top: 5px; font-size: 7px; letter-spacing: .6px;
  }
  .club-badge {
    position: absolute; left: 50%; top: 438px; transform: translateX(-50%);
    width: 140px; height: 140px; border-radius: 50%;
    background: var(--white);
    display: flex; align-items: center; justify-content: center;
    text-align: center; color: var(--navy);
    font-size: 15px; font-weight: 700; line-height: 1.15; padding: 18px;
  }
  .catalog-title {
    position: absolute; left: 0; right: 0; top: 622px;
    text-align: center; color: var(--white);
  }
  .catalog-title .rule {
    display: block; height: 1px; margin: 0 auto;
    width: 360px;
    background: linear-gradient(90deg, transparent, var(--rule-red) 25%, var(--rule-red) 75%, transparent);
  }
  .catalog-title .season {
    display: block; margin-top: 8px;
    font-size: 34px; font-weight: 400; letter-spacing: 1px; line-height: 1;
  }
  .catalog-title .word {
    display: block; margin: 2px 0 6px;
    font-size: 62px; font-weight: 700; letter-spacing: 2px; line-height: 1;
  }
</style>
</head>
<body>
<main class="stage">
  <article class="cover">
    <div class="cover-photo" role="img" aria-label="Photo of a snowboarder carving powder down a wide snowy slope with frosted trees, a snow-capped volcano and valley behind"></div>

    <svg class="cover-curves" viewBox="0 0 540 764" aria-hidden="true">
      <path d="M0 560 C 160 520, 330 540, 540 455 L540 764 L0 764 Z" fill="var(--white)"/>
      <path d="M0 574 C 170 548, 340 560, 540 478 L540 764 L0 764 Z" fill="var(--snow-shade)" opacity=".5"/>
      <path d="M0 582 C 180 560, 350 572, 540 498 L540 764 L0 764 Z" fill="var(--navy)"/>
      <path d="M0 700 L540 690 L540 764 L0 764 Z" fill="var(--navy-deep)" opacity=".35"/>
    </svg>

    <div class="lodge-mark">
      <span class="mark-square"></span>
      <div class="mark-name">Silver Lantern Journeys</div>
      <div class="mark-line">NISEKO · JAPAN · SILVERLANTERNJOURNEYS.COM</div>
    </div>

    <div class="club-badge">Kestrel Ridge Alpine Society</div>

    <h1 class="catalog-title">
      <span class="rule"></span>
      <span class="season">2017-18 PRODUCT</span>
      <span class="word">CATALOG</span>
      <span class="rule"></span>
    </h1>
  </article>
</main>
</body>
</html>
```